Business Card Design

I already have a company logo for my company. I have a logo for the manufacturer we represent. I want a professional business card design.

```html
<!DOCTYPE html>
<html lang="en">
<head>
<meta charset="utf-8">
<title>Signal Guard LLC – Business Card</title>
<link href="https://fonts.googleapis.com/css2?family=Lato:wght@400;700;900&family=Michroma&display=swap" rel="stylesheet">
<style>
  :root{
    --backdrop:#d9d9db;
    --card-dark:#1f1f20;
    --card-mid:#2c2c2e;
    --edge-gold:#e0a712;
    --gold:#d4a017;
    --gold-deep:#b8860b;
    --red:#e2202a;
    --silver-light:#f2f2f2;
    --silver-mid:#bdbdbd;
    --silver-dark:#8a8a8a;
    --text-light:#f0f0f0;
    --text-dark:#1a1a1a;
  }
  *{box-sizing:border-box;margin:0;padding:0}
  html,body{width:1200px;height:982px;overflow:hidden}
  body{background:var(--backdrop);font-family:'Lato',sans-serif;position:relative}

  .card{
    position:absolute;left:232px;width:735px;height:420px;border-radius:22px;overflow:hidden;
    background:radial-gradient(ellipse at 50% 40%,var(--card-mid),var(--card-dark) 75%);
    box-shadow:0 4px 0 var(--edge-gold),0 14px 30px rgba(0,0,0,.35);
  }
  .card--front{top:40px}
  .card--back{top:510px}

  .brand{display:flex;align-items:center;gap:14px;color:var(--red);font-family:'Lato',sans-serif;font-weight:900;letter-spacing:2px;text-transform:uppercase;white-space:nowrap}
  .brand__mark{background:var(--gold);flex:none}
  .card--front .brand{position:absolute;left:50%;top:50%;transform:translate(-50%,-50%);font-size:44px}
  .card--front .brand__mark{width:40px;height:40px}

  .name-band{
    position:absolute;left:0;top:92px;width:735px;height:66px;
    background:linear-gradient(90deg,var(--silver-light) 0%,var(--silver-mid) 55%,var(--silver-dark) 80%,var(--silver-light) 100%);
  }
  .name{
    position:absolute;left:58px;top:106px;font-family:'Michroma',sans-serif;font-weight:400;font-size:32px;
    color:var(--red);letter-spacing:2px;text-transform:uppercase;
  }
  .title-tab{
    position:absolute;left:0;top:158px;width:270px;height:42px;background:var(--gold);
    clip-path:polygon(0 0,100% 0,88% 100%,0 100%);
    color:var(--text-dark);font-size:20px;line-height:42px;padding-left:50px;
  }
  .card--back .brand{position:absolute;right:36px;top:176px;font-size:26px}
  .card--back .brand__mark{width:24px;height:24px}

  .contacts{position:absolute;left:40px;top:250px;list-style:none}
  .contacts li{display:flex;align-items:center;gap:14px;color:var(--text-light);font-size:20px;height:32px}
  .contacts svg{width:18px;height:18px;fill:var(--red);flex:none}

  .address{position:absolute;right:40px;bottom:34px;text-align:right;color:var(--text-light);font-size:19px;line-height:28px}
  .address__company{color:var(--red)}
</style>
</head>
<body>

<section class="card card--front" aria-label="Card front">
  <div class="brand"><span class="brand__mark"></span>Signal Guard LLC</div>
</section>

<section class="card card--back" aria-label="Card back">
  <div class="name-band"></div>
  <h1 class="name">John Smith</h1>
  <div class="title-tab">Founder &amp; CEO</div>
  <div class="brand"><span class="brand__mark"></span>Signal Guard LLC</div>

  <ul class="contacts">
    <li>
      <svg viewBox="0 0 24 24" aria-hidden="true"><path d="M6.6 10.8a15 15 0 0 0 6.6 6.6l2.2-2.2a1 1 0 0 1 1-.25 11.4 11.4 0 0 0 3.6.57 1 1 0 0 1 1 1V20a1 1 0 0 1-1 1A17 17 0 0 1 3 4a1 1 0 0 1 1-1h3.5a1 1 0 0 1 1 1c0 1.25.2 2.45.57 3.6a1 1 0 0 1-.25 1z"/></svg>
      (123) 456-7890
    </li>
    <li>
      <svg viewBox="0 0 24 24" aria-hidden="true"><path d="M7 1h10a2 2 0 0 1 2 2v18a2 2 0 0 1-2 2H7a2 2 0 0 1-2-2V3a2 2 0 0 1 2-2zm0 3v14h10V4zm5 15.5a1.2 1.2 0 1 0 0 2.4 1.2 1.2 0 0 0 0-2.4z"/></svg>
      (123) 456-7890
    </li>
    <li>
      <svg viewBox="0 0 24 24" aria-hidden="true"><path d="M6 2h12v5H6zM4 8h16a2 2 0 0 1 2 2v7h-4v5H6v-5H2v-7a2 2 0 0 1 2-2zm4 7v5h8v-5z"/></svg>
      (123) 456-7890
    </li>
    <li>
      <svg viewBox="0 0 24 24" aria-hidden="true"><path d="M2 4h20v16H2zm2 2v.5l8 5.5 8-5.5V6zm0 3v9h16V9l-8 5.5z"/></svg>
      info@yourwebsitehere.com
    </li>
  </ul>

  <address class="address" style="font-style:normal">
    <div class="address__company">Signal Guard LLC</div>
    <div>423 Street Address Here, City</div>
    <div>State &amp; ZIP Code Country</div>
    <div>www.yourwebsitehere.com</div>
  </address>
</section>

</body>
</html>
```